Travel Agency Website - Simple General

Need a 7 page simple design that is pretty repetitive. Need to be able to load quickly that is SEO optimized. Trying to give ideas on what they can do, be personal as we are local, but at the same time come across as professional and get information easily with little burden.

- Landing Page
- Brimwell Vacations Page
- Family Trips
- Road Trips from Texas
- Other Destinations
- About Us Page
- Contact Us Page

Target Market(s)

Families

Coding

Coded - Design and coding required

Number of Pages Required

5+ page

Colors

Designer to choose colors to be used in the design.

Requirements
Must have
• Like it to flow easily with our logo. Use that for colors, etc.

```html
<!DOCTYPE html>
<html lang="en">
<head>
<meta charset="utf-8">
<title>Wanderlight Journeys Travel Co.</title>
<link href="https://fonts.googleapis.com/css2?family=Great+Vibes&family=Inter:wght@400;500;600;700&display=swap" rel="stylesheet">
<style>
:root{
  --teal:#1f6e72;
  --teal-soft:#7cc3c8;
  --teal-pale:#cde9ea;
  --ink:#0f3a45;
  --gold:#f0c56e;
  --gold-dark:#c99a47;
  --cream:#fbf8f3;
  --text:#3a4a50;
}
*{box-sizing:border-box;margin:0;padding:0}
html,body{width:1200px;height:3444px;overflow:hidden}
body{position:relative;background:var(--cream);font-family:'Inter',sans-serif;color:var(--text)}
.abs{position:absolute}
.script{font-family:'Great Vibes',cursive;color:var(--ink);font-weight:400;line-height:1}
.btn{position:absolute;display:flex;align-items:center;justify-content:center;gap:12px;height:46px;border:1.5px solid var(--teal);border-radius:23px;background:rgba(255,255,255,.85);font-weight:600;font-size:16px;color:var(--ink);text-decoration:none}
.btn svg{width:16px;height:16px;stroke:currentColor;stroke-width:2.2;fill:none}
.btn.solid{background:var(--teal);color:#fff;border-color:var(--gold)}

/* hero */
.hero-photo{left:0;top:0;width:1200px;height:880px;
  background:linear-gradient(180deg,#c9d6da 0%,#efe3cf 20%,#f5d9ae 40%,#9fc7c6 52%,#5fb0b5 66%,#4aa3ab 78%,rgba(120,190,195,.6) 90%,var(--cream) 100%)}
.header-contact{top:30px;font-size:19px;color:var(--ink)}
.header-contact strong{display:block;font-size:17px;font-weight:600;color:var(--teal)}
.icon-ring{position:absolute;width:58px;height:58px;border-radius:50%;border:2px solid var(--teal);background:#fff;display:flex;align-items:center;justify-content:center}
.icon-ring svg{width:20px;height:20px;fill:var(--teal)}
.brand{left:520px;top:20px;width:160px;height:66px;display:flex;align-items:center;justify-content:center;gap:6px;font-weight:600;font-size:15px;color:var(--teal);text-align:center;line-height:1.2}
.brand i{width:10px;height:10px;border-radius:50%;background:var(--teal);flex:none}
.nav{left:114px;top:116px;width:968px;height:38px;border-bottom:1.5px solid rgba(31,110,114,.5);background:linear-gradient(90deg,rgba(255,255,255,0),rgba(255,255,255,.45) 15%,rgba(255,255,255,.45) 85%,rgba(255,255,255,0));display:flex;align-items:center;padding-left:69px}
.nav a{font-size:14px;color:#1d2a2e;text-decoration:none;padding:0 14px;height:38px;display:flex;align-items:center}
.nav a.active{background:var(--teal);color:#fff}
.hero-title{left:0;width:1200px;top:265px;text-align:center;font-size:98px}
.hero-sub{left:0;width:1200px;top:385px;text-align:center;font-size:19px;color:var(--ink);letter-spacing:.5px}
.arrow{position:absolute;top:605px;width:40px;height:40px;border-radius:50%;background:#fff;display:flex;align-items:center;justify-content:center;box-shadow:0 2px 6px rgba(0,0,0,.12)}
.arrow svg{width:14px;height:14px;stroke:var(--ink);stroke-width:2.5;fill:none}
.ornament{position:absolute;border-radius:50%;background:radial-gradient(ellipse at center,rgba(31,110,114,.14),rgba(31,110,114,0) 70%)}

/* about */
.about-ring{left:128px;top:939px;width:446px;height:446px;border-radius:50%;border:3px solid var(--gold);background:var(--cream)}
.about-photo{left:155px;top:966px;width:392px;height:392px;border-radius:50%;background:linear-gradient(180deg,#8b8f9c 0%,#e7a869 35%,#f4c081 50%,#6d8c98 65%,#1f5262 100%)}
.sparkle{position:absolute;width:20px;height:20px;fill:var(--gold-dark)}
.about-title{left:612px;top:965px;font-size:86px}
.about-text{left:612px;top:1060px;width:444px;font-size:15.5px;line-height:24px;text-align:justify}
.about-text p+p{margin-top:24px}

/* categories */
.cat-title{left:0;width:1200px;top:1505px;text-align:center;font-size:86px}
.card{position:absolute;top:1619px;width:282px;height:356px;border:3px solid var(--gold);border-radius:22px;overflow:hidden}
.card .fill{position:absolute;inset:0}
.card h3{position:absolute;top:24px;left:0;width:100%;text-align:center;font-size:19px;font-weight:400;color:var(--ink);line-height:28px}
.card .btn{left:47px;top:286px;width:187px;height:45px;font-size:16px}

/* cta */
.cta-title{left:0;width:1200px;top:2110px;text-align:center;font-size:86px;line-height:84px}
.cta-text{left:180px;width:840px;top:2310px;text-align:center;font-size:15.5px;line-height:24px}

/* contact pill */
.wash{left:0;top:2480px;width:1200px;height:740px;
  background:radial-gradient(ellipse 60% 40% at 50% 30%,rgba(95,176,181,.75),rgba(95,176,181,0) 70%),radial-gradient(ellipse 55% 30% at 30% 80%,rgba(120,190,195,.6),rgba(120,190,195,0) 70%),radial-gradient(ellipse 50% 35% at 80% 75%,rgba(95,176,181,.55),rgba(95,176,181,0) 70%)}
.pill{left:64px;top:2663px;width:1072px;height:311px;border-radius:156px;border:3px solid var(--gold);background:var(--cream)}
.pill-title{left:167px;top:2745px;font-size:80px;line-height:80px}
.contact-row{position:absolute;left:655px;display:flex;align-items:center;gap:16px}
.contact-row .dot{width:56px;height:56px;border-radius:50%;background:var(--teal);display:flex;align-items:center;justify-content:center}
.contact-row .dot svg{width:20px;height:20px;fill:#fff}
.contact-row span{font-size:19px;color:var(--ink);display:block}
.contact-row strong{font-size:21px;font-weight:600;color:var(--teal);display:block;margin-top:4px}
.divider{left:657px;top:2812px;width:400px;height:1px;background:#cfd7d6}

/* footer */
.foot-brand{left:147px;top:3190px;width:234px;height:200px;display:flex;align-items:center;justify-content:center;gap:10px;font-size:24px;font-weight:600;color:var(--teal);text-align:center;line-height:1.25}
.foot-brand i{width:14px;height:14px;border-radius:50%;background:var(--teal);flex:none}
.foot-links{left:438px;top:3212px;font-size:19px;color:var(--ink)}
.foot-links a{color:var(--ink);text-decoration:none}
.foot-links b{font-weight:400;margin:0 22px}
.follow{left:438px;top:3270px;display:flex;align-items:center;gap:12px;font-size:19px;font-weight:700;color:var(--ink)}
.social{width:40px;height:40px;border-radius:50%;border:1.5px solid var(--teal-soft);background:#fff}
.social.on{background:var(--teal);border-color:var(--teal)}
.copy{left:438px;top:3341px;font-size:19px;color:var(--ink)}
.code{left:1122px;top:3354px;font-size:11px;color:var(--ink)}
</style>
</head>
<body>
<svg width="0" height="0" style="position:absolute">
  <defs>
    <symbol id="go" viewBox="0 0 16 16"><path d="M2 8h11M9 4l4 4-4 4"/></symbol>
    <symbol id="phone" viewBox="0 0 24 24"><path d="M6.6 10.8a15.1 15.1 0 0 0 6.6 6.6l2.2-2.2a1 1 0 0 1 1-.25 11.4 11.4 0 0 0 3.6.57 1 1 0 0 1 1 1V20a1 1 0 0 1-1 1A17 17 0 0 1 3 4a1 1 0 0 1 1-1h3.5a1 1 0 0 1 1 1c0 1.25.2 2.45.57 3.57a1 1 0 0 1-.25 1z"/></symbol>
    <symbol id="mail" viewBox="0 0 24 24"><path d="M3 5h18a1 1 0 0 1 1 1v1l-10 6L2 7V6a1 1 0 0 1 1-1zm-1 4.3 10 6 10-6V18a1 1 0 0 1-1 1H3a1 1 0 0 1-1-1z"/></symbol>
    <symbol id="star" viewBox="0 0 20 20"><path d="M10 0 12 8 20 10 12 12 10 20 8 12 0 10 8 8z"/></symbol>
  </defs>
</svg>

<!-- hero -->
<div class="abs hero-photo" role="img" aria-label="Sunset sky with clouds over turquoise ocean waves, fading into soft teal watercolor"></div>

<div class="abs header-contact" style="left:108px;text-align:right;width:298px">Email:<strong>hello@wanderlightjourneys.com</strong></div>
<div class="icon-ring" style="left:423px;top:24px"><svg><use href="#mail"/></svg></div>
<div class="abs brand"><i></i>Wanderlight Journeys</div>
<div class="icon-ring" style="left:710px;top:24px"><svg><use href="#phone"/></svg></div>
<div class="abs header-contact" style="left:781px">Phone:<strong style="font-size:19px">555.018.2046</strong></div>

<nav class="abs nav">
  <a class="active" href="#">Home</a>
  <a href="#">Brimwell Vacations</a>
  <a href="#">Family Trips</a>
  <a href="#">Road Trips from Texas</a>
  <a href="#">Other Destinations</a>
  <a href="#">About Us</a>
  <a href="#">Contact Us</a>
</nav>

<h1 class="abs script hero-title">Wanderlight Journeys</h1>
<p class="abs hero-sub">YOUR JOURNEY BEGINS HERE</p>
<a class="btn" href="#" style="left:473px;top:431px;width:254px">Explore Destinations <svg><use href="#go"/></svg></a>
<div class="arrow" style="left:556px"><svg viewBox="0 0 14 14"><path d="M9 2 4 7l5 5"/></svg></div>
<div class="arrow" style="left:604px"><svg viewBox="0 0 14 14"><path d="M5 2l5 5-5 5"/></svg></div>

<div class="ornament" role="img" aria-label="Decorative flight path ornament" style="left:0;top:690px;width:760px;height:220px"></div>

<!-- about -->
<div class="abs about-ring"></div>
<div class="abs about-photo" role="img" aria-label="Couple on a wooden deck watching a sunset over the sea"></div>
<svg class="sparkle" style="left:590px;top:965px"><use href="#star"/></svg>
<h2 class="abs script about-title">About Us</h2>
<div class="abs about-text">
  <p>Lorem ipsum dolor sit amet, consectetur adipiscing elit, sed do eiusmod tempor incididunt ut labore et dolore magna aliqua. Ut enim ad minim veniam, quis nostrud exercitation ullamco laboris nisi ut aliquip ex ea commodo consequat. Duis aute irure dolor in reprehenderit in voluptate velit esse cillum dolore eu fugiat nulla pariatur.</p>
  <p>Excepteur sint occaecat cupidatat non proident, sunt in culpa qui officia deserunt mollit anim id est laborum.</p>
</div>
<a class="btn" href="#" style="left:612px;top:1295px;width:189px">Learn More <svg><use href="#go"/></svg></a>

<!-- categories -->
<div class="abs" style="left:900px;top:1400px;width:300px;height:300px;background:radial-gradient(circle at 80% 40%,rgba(124,195,200,.5),rgba(124,195,200,0) 65%)"></div>
<svg class="sparkle" style="left:590px;top:1474px"><use href="#star"/></svg>
<h2 class="abs script cat-title">Travel Categories</h2>

<div class="card" style="left:7px">
  <div class="fill" role="img" aria-label="Cruise ship on calm water beneath a city skyline" style="background:linear-gradient(180deg,#fff 0%,#dfe7f1 25%,#8ea3c0 45%,#4a5f86 70%,#1c3360 100%)"></div>
  <h3>Brimwell Vacations<br>Land &amp; Sea</h3>
  <a class="btn" href="#">Explore Magic <svg><use href="#go"/></svg></a>
</div>
<div class="card" style="left:309px">
  <div class="fill" role="img" aria-label="Family walking hand in hand along a beach at sunset" style="background:linear-gradient(180deg,#fff 0%,#e8ecef 25%,#f1d8b6 50%,#d9c3a5 75%,#bda585 100%)"></div>
  <h3>Family Trips</h3>
  <a class="btn solid" href="#">Plan Together <svg><use href="#go"/></svg></a>
</div>
<div class="card" style="left:609px">
  <div class="fill" role="img" aria-label="Camper van parked beside a mountain lake" style="background:linear-gradient(180deg,#fff 0%,#dde7ea 25%,#7fa9b4 45%,#4d8a8c 60%,#8eb3ba 75%,#5b8c8f 100%)"></div>
  <h3>Powered by Pine County<br>Van Rentals</h3>
  <a class="btn" href="#">Hit the Road <svg><use href="#go"/></svg></a>
</div>
<div class="card" style="left:911px">
  <div class="fill" role="img" aria-label="Traveler standing in a rocky cove with turquoise water" style="background:linear-gradient(180deg,#fff 0%,#e5e9e6 22%,#7c8a7a 45%,#5f7d68 60%,#4fb2b0 78%,#b49a86 100%)"></div>
  <h3>Other Destinations</h3>
  <a class="btn" href="#">Discover More <svg><use href="#go"/></svg></a>
</div>

<!-- cta -->
<div class="ornament" role="img" aria-label="Decorative looping path ornament" style="left:970px;top:2020px;width:230px;height:215px"></div>
<svg class="sparkle" style="left:590px;top:2086px"><use href="#star"/></svg>
<h2 class="abs script cta-title">Let's Make Every<br>Journey Unforgettable</h2>
<p class="abs cta-text">Lorem ipsum dolor sit amet, consectetur adipiscing elit, sed do eiusmod tempor incididunt ut labore et dolore magna aliqua. Ut enim ad minim veniam, quis nostrud exercitation ullamco laboris nisi ut aliquip ex ea commodo reprehenderit in voluptate velit esse cillum dolore eu fugiat nulla pariatur.</p>
<a class="btn" href="#" style="left:505px;top:2410px;width:190px">Contact Us <svg><use href="#go"/></svg></a>

<!-- contact pill -->
<div class="abs wash"></div>
<div class="abs pill"></div>
<svg class="sparkle" style="left:183px;top:2718px"><use href="#star"/></svg>
<h2 class="abs script pill-title">Ready to Start<br>Your Journey?</h2>
<div class="contact-row" style="top:2730px"><div class="dot"><svg><use href="#phone"/></svg></div><div><span>Phone:</span><strong>555.018.2046</strong></div></div>
<div class="abs divider"></div>
<div class="contact-row" style="top:2842px"><div class="dot"><svg><use href="#mail"/></svg></div><div><span>Email:</span><strong>hello@wanderlightjourneys.com</strong></div></div>

<div class="ornament" role="img" aria-label="Decorative flight path ornament" style="left:700px;top:3030px;width:500px;height:130px"></div>

<!-- footer -->
<div class="abs foot-brand"><i></i>Wanderlight<br>Journeys</div>
<div class="abs foot-links"><a href="#">Home</a><b>/</b><a href="#">All 4 Travel Categories</a><b>/</b><a href="#">About Us</a><b>/</b><a href="#">Contact Us</a></div>
<div class="abs follow">Follow Us:<span class="social on" role="img" aria-label="Social profile"></span><span class="social" role="img" aria-label="Photo profile"></span></div>
<p class="abs copy">© 2026 Wanderlight Journeys Travel Co. All Rights Reserved.</p>
<span class="abs code">C38</span>
</body>
</html>
```